Brightway Haul & Upkeep Services, are a company that offers a 'one stop shop' pre-move clean up a

I have already selected a logo which I would like on the front of the business cards along with phone numbers, web address and email which are:
0487650392
www.brightwayhaul.com.au
brightwayhaulandupkeep@mailbox.example

On the back of the card I would like to list some of the types of service we offer (clean - move - repairs/maintenance) which are:
CLEAN - windows, gutters, solar panels, driveways/paths, carpets.
MOVE - Small/medium size house/office moves, large item pick-up & delivery, yard clean-up and removal.
General maintenance and repairs.

I would like the blue logo on a gray background.

Thanks

```html
<!DOCTYPE html>
<html lang="en">
<head>
<meta charset="utf-8">
<title>Brightway Haul &amp; Upkeep Services — Business Cards</title>
<link href="https://fonts.googleapis.com/css2?family=Exo+2:wght@600;700&family=Source+Sans+3:wght@400&display=swap" rel="stylesheet">
<style>
  :root {
    --brand-blue: #1f6bb5;
    --card-gray: #c4c4c4;
    --rule-dark: #2a2a2a;
    --ink: #1f1f1f;
    --backdrop: #ecebe8;
  }
  html, body {
    margin: 0;
    padding: 0;
    width: 1200px;
    height: 1006px;
    overflow: hidden;
    background: var(--backdrop);
  }
  .card {
    position: absolute;
    background: var(--card-gray);
    box-shadow: 0 0 0 1px rgba(0,0,0,0.25);
    overflow: hidden;
  }
  .card--front { left: 43px; top: 43px; width: 783px; height: 448px; }
  .card--back  { left: 325px; top: 526px; width: 782px; height: 446px; }

  .front-band {
    position: absolute; left: 0; top: 0; width: 100%; height: 113px;
    background: var(--brand-blue);
  }
  .front-rule {
    position: absolute; left: 0; top: 115px; width: 100%; height: 4px;
    background: var(--rule-dark);
  }

  .brand-name {
    position: absolute; left: 0; width: 100%;
    text-align: center;
    font-family: "Exo 2", sans-serif;
    font-weight: 700;
    color: var(--brand-blue);
    text-transform: uppercase;
    line-height: 1.05;
    margin: 0;
  }
  .brand-name .line-main { display: block; font-size: 64px; letter-spacing: 1px; }
  .brand-name .line-sub  { display: block; font-size: 30px; letter-spacing: 0.5px; }
  .card--front .brand-name { top: 145px; }
  .card--back .brand-name  { top: 120px; }

  .contact-list {
    position: absolute; left: 0; top: 316px; width: 100%;
    list-style: none; margin: 0; padding: 0;
    text-align: center;
    font-family: "Source Sans 3", sans-serif;
    font-size: 22px;
    color: var(--ink);
  }
  .contact-list li { height: 34px; line-height: 34px; }
  .contact-list svg { width: 16px; height: 16px; vertical-align: -2px; margin-right: 8px; }

  .services-heading {
    position: absolute; left: 0; top: 290px; width: 100%;
    margin: 0; text-align: center;
    font-family: "Exo 2", sans-serif; font-weight: 700;
    font-size: 32px; letter-spacing: 2px;
    color: var(--brand-blue);
  }
  .service-list {
    position: absolute; left: 0; width: 100%;
    margin: 0; padding: 0; list-style: none;
    text-align: center;
    font-family: "Exo 2", sans-serif; font-weight: 600;
    font-size: 24px; color: var(--ink);
  }
  .service-list--top { top: 352px; }
  .service-list--bottom { top: 392px; }
  .service-list li { display: inline-block; margin: 0 8px; }
  .service-list li::before { content: "• "; color: var(--brand-blue); }
</style>
</head>
<body>
  <section class="card card--front" aria-label="Card front">
    <div class="front-band"></div>
    <div class="front-rule"></div>
    <h1 class="brand-name">
      <span class="line-main">Brightway Haul</span>
      <span class="line-sub">&amp; Upkeep Services</span>
    </h1>
    <ul class="contact-list">
      <li>
        <svg viewBox="0 0 16 16" aria-hidden="true"><circle cx="8" cy="8" r="7" fill="none" stroke="#1f6bb5" stroke-width="1.6"/><path d="M5.5 4.5l1.5 0 .6 2-1 .8a5 5 0 0 0 2.1 2.1l.8-1 2 .6v1.5c-3.5.5-6.5-2.5-6-6z" fill="#1f6bb5"/></svg>0487650392
      </li>
      <li>
        <svg viewBox="0 0 16 16" aria-hidden="true"><circle cx="8" cy="8" r="7" fill="#1f6bb5"/><path d="M1 8h14M8 1c-3 3.5-3 10.5 0 14M8 1c3 3.5 3 10.5 0 14" stroke="#c4c4c4" stroke-width="1" fill="none"/></svg>www.brightwayhaul.com.au
      </li>
      <li>
        <svg viewBox="0 0 16 16" aria-hidden="true"><rect x="1" y="3" width="14" height="10" rx="1" fill="#1f6bb5"/><path d="M1.5 4l6.5 5 6.5-5" stroke="#c4c4c4" stroke-width="1.2" fill="none"/></svg>brightwayhaulandupkeep@mailbox.example
      </li>
    </ul>
  </section>

  <section class="card card--back" aria-label="Card back">
    <h2 class="brand-name">
      <span class="line-main">Brightway Haul</span>
      <span class="line-sub">&amp; Upkeep Services</span>
    </h2>
    <h3 class="services-heading">Services we offer</h3>
    <ul class="service-list service-list--top">
      <li>Clean</li>
      <li>Move</li>
    </ul>
    <ul class="service-list service-list--bottom">
      <li>General Maintenance And Repairs.</li>
    </ul>
  </section>
</body>
</html>
```